Black Car Limousine transportation business in Naples Florida

Always stand for my reliability and RVD stands for Love, K and M are the first initials of my children's names. It should show professionalism and a dedication to customer service. We keep our clients identities private. Show our professionalism. We are Black car Black tie company. We service transportation on a reserve basis to and from residents, airports, casinos, hotels,

Target Market(s)

It is a Private car service. High end clients. Businesses, Celebrity and athletes. Service to airports, hotels, special events.

Industry/Entity Type

Business

Contact Information for Business Card

A pearl metallic or Luster card. Standard business card size. Would like the name, Company email, show we take credit cards and phone number. Currently I don't have a website but will like to add later.

Logo Text

STEADFAST RVD TRANSPORTATION

Font styles to use
Serif

Colors
eaeaea
000000

Requirements
Must have
• Must have Company email, show we take credit cards and phone number. Currently I don't have a website but will like to add later.
Nice to have
• Would like to stay with a black and white theme. Open to some color trim.
Should not have
• Open to suggestions

```html
<!DOCTYPE html>
<html lang="en">
<head>
<meta charset="UTF-8">
<title>Steadfast RVD Transportation – Business Card</title>
<link href="https://fonts.googleapis.com/css2?family=Open+Sans:ital,wght@0,400;0,600;0,700;1,700&display=swap" rel="stylesheet">
<style>
  :root {
    --backdrop: #a9a9a9;
    --card-white: #ffffff;
    --card-black: #000000;
    --ink: #111111;
    --ink-soft: #444444;
    --trim-gray: #8c8c8c;
    --divider: #cfcfcf;
    --logo-dark: #7d7d7d;
    --logo-light: #cfcfcf;
    --vehicle-dark: #1a1a1a;
    --vehicle-mid: #4a4a4a;
  }
  * { box-sizing: border-box; margin: 0; padding: 0; }
  html, body {
    width: 1105px; height: 1200px; overflow: hidden;
    background: var(--backdrop);
    font-family: "Open Sans", Arial, sans-serif;
  }
  .card {
    position: absolute; left: 193px; width: 720px; height: 410px;
    box-shadow: 0 4px 10px rgba(0,0,0,0.35);
    overflow: hidden;
  }
  .card--front { top: 167px; background: var(--card-white); }
  .card--back { top: 621px; background: var(--card-black); }

  .vehicle-photo {
    position: absolute; border-radius: 10px 14px 6px 6px;
  }
  .card--front .vehicle-photo {
    left: 59px; top: 195px; width: 124px; height: 52px;
    background: linear-gradient(180deg, var(--vehicle-mid), var(--vehicle-dark));
  }
  .card--back .vehicle-photo {
    left: 135px; top: 177px; width: 180px; height: 76px;
    background: linear-gradient(180deg, #5c5c5c, #141414);
  }

  .brand-name {
    position: absolute; font-weight: 700; text-transform: uppercase;
    line-height: 1.1; letter-spacing: 0.5px;
  }
  .card--front .brand-name {
    left: 195px; top: 192px; width: 185px; font-size: 19px; color: var(--logo-dark);
  }
  .card--back .brand-name {
    left: 330px; top: 162px; width: 260px; font-size: 27px; color: var(--logo-light);
  }

  .divider {
    position: absolute; left: 400px; top: 127px; width: 1px; height: 155px;
    background: var(--divider);
  }
  .contact-block { position: absolute; left: 432px; top: 134px; }
  .person-name { font-size: 25px; font-weight: 600; color: var(--ink); line-height: 1.2; }
  .person-role { font-size: 18px; color: var(--ink-soft); margin-top: 2px; }
  .contact-list { list-style: none; margin-top: 18px; }
  .contact-list li {
    display: flex; align-items: center; gap: 10px;
    font-size: 18px; color: var(--ink-soft); height: 28px;
  }
  .contact-list svg { width: 17px; height: 17px; fill: var(--ink); flex: none; }

  .trim-band { position: absolute; left: 0; bottom: 0; width: 720px; height: 26px; }

  .payment-note {
    position: absolute; left: 0; width: 720px; top: 337px;
    display: flex; justify-content: center; align-items: center; gap: 8px;
    color: #ffffff; font-size: 19px; font-weight: 700; font-style: italic;
  }
  .payment-note svg { width: 26px; height: 18px; }
</style>
</head>
<body>
  <section class="card card--front">
    <div class="vehicle-photo" role="img" aria-label="Photo of a black luxury SUV"></div>
    <div class="brand-name">Steadfast RVD Transportation</div>
    <div class="divider"></div>
    <div class="contact-block">
      <div class="person-name">MARCUS DELANEY</div>
      <div class="person-role">CEO/Founder</div>
      <ul class="contact-list">
        <li><svg viewBox="0 0 24 24"><path d="M6.6 10.8a15.1 15.1 0 0 0 6.6 6.6l2.2-2.2a1 1 0 0 1 1-.25 11.4 11.4 0 0 0 3.6.57 1 1 0 0 1 1 1V20a1 1 0 0 1-1 1A17 17 0 0 1 3 4a1 1 0 0 1 1-1h3.5a1 1 0 0 1 1 1c0 1.25.2 2.45.57 3.57a1 1 0 0 1-.25 1z"/></svg>239 555 0147</li>
        <li><svg viewBox="0 0 24 24"><path d="M2 5h20v14H2z M4 7v.5l8 5 8-5V7l-8 5z" fill-rule="evenodd"/></svg>ride@steadfastrvd.com</li>
        <li><svg viewBox="0 0 24 24"><circle cx="12" cy="12" r="10"/><path d="M2 12h20M12 2c3 3 3 17 0 20M12 2c-3 3-3 17 0 20" stroke="#fff" stroke-width="1.4" fill="none"/></svg>www.steadfastrvd.com</li>
      </ul>
    </div>
    <svg class="trim-band" viewBox="0 0 720 26" aria-hidden="true">
      <polygon points="0,0 475,0 468,26 0,26" fill="var(--card-black)"/>
      <polygon points="482,0 720,0 720,26 475,26" fill="var(--trim-gray)"/>
    </svg>
  </section>

  <section class="card card--back">
    <div class="vehicle-photo" role="img" aria-label="Photo of a black luxury SUV"></div>
    <div class="brand-name">Steadfast RVD Transportation</div>
    <div class="payment-note">
      <svg viewBox="0 0 26 18" aria-hidden="true"><rect x="1" y="1" width="24" height="16" rx="2" fill="#fff"/><rect x="1" y="5" width="24" height="3" fill="#000"/><rect x="4" y="11" width="8" height="2" fill="#000"/></svg>
      We accept credit cards
    </div>
  </section>
</body>
</html>
```